Vexa - Booking activities for Kids and Adults.

The app allows booking of Kid's activities for a given date/time.
The app lists activities offered via various clubs (vendors) which a user can book for their kids.
The users can browse various clubs and their offered activities. The users can manage their kid's profiles.
Need a whole new look to the app. The existing app can be checked out at
https://apps.storefrontexample.test/details?id=com.vexakw
https://apps.appmarketexample.test/us/app/vexa-فيكسا/id7302958146?ls=1
Try using the app as Guest.

Target Market(s)

Kuwait

Font styles to use
Serif
Sans Serif

Requirements
Must have
• Home Screens
The home page should have everything from the existing app and a quick area to change between different kid's profile to see activities matching their interests ONLY. In the current version, there's no switch profile and hence we are showing the name tags on the activities.

We are also going to build ecommerce so we need that ecommerce look and feel.
Kindly maintain the image aspect ratio from the current app so the new version doesn't require new images.

Need a complete new innovative designs - Keep the color scheme same.
The designs should be minimalistic and image oriented. The design should be done in XD. The designs should be submitted in both light and dark theme.
Reference to be used - http://plimtor.example

D.M for more info if needed.

```html
<!DOCTYPE html>
<html lang="en">
<head>
<meta charset="utf-8">
<title>Vexa – Home</title>
<link rel="stylesheet" href="https://fonts.googleapis.com/css2?family=Poppins:wght@400;500;600;700&display=swap">
<style>
  :root {
    --page-bg: #f7f7f7;
    --surface: #ffffff;
    --ink: #333333;
    --ink-soft: #6b6b6b;
    --ink-muted: #8f8f8f;
    --field: #efefef;
    --line: #e6e6e6;
    --orange: #ff8c3f;
    --yellow: #fdc62a;
    --teal: #42c4c1;
    --purple: #a64b8c;
    --blue: #02a3e3;
    --brand: #1fc7c5;
    --photo-warm-a: #6b4a36;
    --photo-warm-b: #b08a68;
    --photo-cool-a: #2f3a38;
    --photo-cool-b: #56625f;
  }
  * { box-sizing: border-box; margin: 0; padding: 0; }
  html, body {
    width: 1200px; height: 2592px; overflow: hidden;
    background: var(--page-bg);
    font-family: "Poppins", sans-serif;
    color: var(--ink);
  }
  .screen { position: relative; width: 1200px; height: 2592px; overflow: hidden; }

  /* Header */
  .app-header {
    position: absolute; left: 0; top: 0; width: 1200px; height: 563px;
    background: var(--surface);
    border-radius: 0 0 100px 100px;
    box-shadow: 0 10px 30px rgba(0,0,0,0.05);
  }
  .status-time { position: absolute; left: 97px; top: 30px; font-size: 47px; font-weight: 500; letter-spacing: -1px; }
  .status-icons { position: absolute; right: 68px; top: 44px; }
  .menu-button { position: absolute; left: 67px; top: 198px; }
  .brand {
    position: absolute; left: 0; right: 0; top: 160px;
    display: flex; align-items: center; justify-content: center; gap: 16px;
  }
  .brand-dot { width: 34px; height: 34px; border-radius: 50%; background: var(--orange); }
  .brand-name { font-size: 110px; font-weight: 600; color: var(--brand); line-height: 1; }
  .cart-button { position: absolute; left: 962px; top: 188px; }
  .filter-button { position: absolute; left: 1066px; top: 200px; }

  .search-bar {
    position: absolute; left: 67px; top: 375px; width: 1063px; height: 117px;
    background: var(--field); border-radius: 59px;
    display: flex; align-items: center; padding-left: 70px;
  }
  .search-placeholder { font-size: 33px; color: var(--ink-soft); }
  .search-button {
    position: absolute; right: 15px; top: 13px; width: 91px; height: 91px;
    border-radius: 50%; background: var(--ink);
    display: flex; align-items: center; justify-content: center;
  }

  /* Section headings */
  .section-title { position: absolute; left: 65px; font-size: 60px; font-weight: 600; letter-spacing: 0.5px; }
  .section-note { position: absolute; right: 68px; font-size: 33px; color: var(--ink-soft); }

  /* Date tiles */
  .date-tile {
    position: absolute; border-radius: 27px; color: #fff;
    display: flex; flex-direction: column; align-items: center; justify-content: center;
    text-align: center;
  }
  .date-tile .tile-title { font-size: 43px; font-weight: 600; line-height: 1.2; }
  .date-tile .tile-sub { font-size: 30px; font-weight: 400; line-height: 1.3; }
  .tile-week { left: 67px; top: 765px; width: 518px; height: 175px; background: var(--orange); }
  .tile-month { left: 608px; top: 765px; width: 520px; height: 175px; background: var(--yellow); }
  .tile-saturday { left: 67px; top: 960px; width: 341px; height: 175px; background: var(--teal); }
  .tile-sunday { left: 427px; top: 960px; width: 341px; height: 175px; background: var(--purple); }
  .tile-pick { left: 787px; top: 960px; width: 341px; height: 175px; background: var(--blue); gap: 6px; }

  /* Activity cards */
  .activity-card {
    position: absolute; left: 67px; width: 1061px;
    background: var(--surface); border-radius: 33px; overflow: hidden;
    box-shadow: 0 6px 24px rgba(0,0,0,0.05);
  }
  .card-cooking { top: 1335px; height: 898px; }
  .card-second { top: 2283px; height: 400px; }
  .activity-photo { position: absolute; left: 0; top: 0; width: 100%; height: 492px; }
  .photo-cooking { background: linear-gradient(135deg, var(--photo-warm-a), var(--photo-warm-b) 60%, #d9d2c8); }
  .photo-portrait { background: linear-gradient(180deg, var(--photo-cool-b), var(--photo-cool-a)); height: 400px; }

  .kid-tags { position: absolute; left: 33px; top: 42px; display: flex; gap: 9px; }
  .kid-tag {
    height: 42px; padding: 0 24px; border-radius: 21px;
    font-size: 25px; font-weight: 600; color: #fff;
    display: flex; align-items: center; letter-spacing: 0.5px;
  }
  .tag-orange { background: var(--orange); }
  .tag-yellow { background: var(--yellow); }
  .tag-blue { background: var(--blue); }
  .tag-purple { background: var(--purple); }

  .activity-meta {
    position: absolute; left: 50px; top: 533px; display: flex; gap: 52px;
    font-size: 30px; color: var(--ink-muted);
  }
  .meta-item { display: flex; align-items: center; gap: 8px; }
  .card-divider { position: absolute; left: 50px; top: 612px; width: 955px; height: 2px; background: var(--line); }
  .activity-price { position: absolute; left: 50px; top: 645px; font-size: 40px; font-weight: 600; color: var(--orange); }
  .activity-title { position: absolute; left: 50px; top: 693px; font-size: 53px; font-weight: 600; letter-spacing: 0.3px; }
  .favourite-button {
    position: absolute; left: 938px; top: 697px; width: 60px; height: 60px; border-radius: 50%;
    background: #e8e8e8; display: flex; align-items: center; justify-content: center;
  }
  .activity-chips { position: absolute; left: 50px; top: 785px; display: flex; gap: 22px; }
  .chip {
    height: 57px; padding: 0 33px; border-radius: 29px;
    font-size: 23px; font-weight: 500; display: flex; align-items: center;
  }
  .chip-vendor { background: #e9e9e9; color: var(--ink); }
  .chip-status { background: var(--teal); color: #fff; }
</style>
</head>
<body>
<main class="screen">

  <header class="app-header">
    <div class="status-time">11:04</div>
    <svg class="status-icons" width="140" height="32" viewBox="0 0 140 32" aria-hidden="true">
      <rect x="0" y="20" width="7" height="10" rx="1.5" fill="#111"/>
      <rect x="11" y="15" width="7" height="15" rx="1.5" fill="#111"/>
      <rect x="22" y="9" width="7" height="21" rx="1.5" fill="#111"/>
      <rect x="33" y="3" width="7" height="27" rx="1.5" fill="#bbb"/>
      <path d="M56 11 a22 22 0 0 1 30 0 M61 17 a14 14 0 0 1 20 0" stroke="#111" stroke-width="4.5" fill="none" stroke-linecap="round"/>
      <circle cx="71" cy="25" r="4" fill="#111"/>
      <rect x="94" y="5" width="40" height="22" rx="6" fill="none" stroke="#111" stroke-width="2.5"/>
      <rect x="97" y="8" width="34" height="16" rx="3.5" fill="#111"/>
      <rect x="136" y="12" width="3" height="8" rx="1.5" fill="#111"/>
    </svg>

    <svg class="menu-button" width="72" height="58" viewBox="0 0 72 58" aria-label="Menu" role="img">
      <path d="M4 4 H68 M20 29 H68 M4 54 H68" stroke="#222" stroke-width="6" stroke-linecap="round"/>
    </svg>

    <div class="brand">
      <span class="brand-dot"></span>
      <span class="brand-name">Vexa</span>
    </div>

    <svg class="cart-button" width="72" height="72" viewBox="0 0 72 72" aria-label="Basket" role="img">
      <circle cx="36" cy="8" r="7" fill="var(--orange)"/>
      <path d="M20 28 L32 14 M52 28 L40 14" stroke="#222" stroke-width="3.5" stroke-linecap="round"/>
      <path d="M4 28 H68 V36 H4 Z" fill="none" stroke="#222" stroke-width="3.5" stroke-linejoin="round"/>
      <path d="M8 36 L14 64 H58 L64 36" fill="none" stroke="#222" stroke-width="3.5" stroke-linejoin="round"/>
      <path d="M24 44 V56 M36 44 V56 M48 44 V56" stroke="#222" stroke-width="3.5" stroke-linecap="round"/>
    </svg>

    <svg class="filter-button" width="64" height="60" viewBox="0 0 64 60" aria-label="Filter" role="img">
      <path d="M3 4 H61 L39 30 V52 L25 58 V30 Z" fill="none" stroke="#222" stroke-width="3.5" stroke-linejoin="round"/>
      <path d="M10 14 H54" stroke="#222" stroke-width="3.5"/>
    </svg>

    <div class="search-bar">
      <span class="search-placeholder">Find a search here...</span>
      <div class="search-button">
        <svg width="38" height="38" viewBox="0 0 38 38" aria-hidden="true">
          <circle cx="16" cy="16" r="11" fill="none" stroke="#fff" stroke-width="4"/>
          <path d="M24 24 L34 34" stroke="#fff" stroke-width="4" stroke-linecap="round"/>
        </svg>
      </div>
    </div>
  </header>

  <h2 class="section-title" style="top:660px;">Find something to do</h2>

  <div class="date-tile tile-week">
    <span class="tile-title">This Week</span>
    <span class="tile-sub">Monday 6th june 2020</span>
  </div>
  <div class="date-tile tile-month">
    <span class="tile-title">This Month</span>
    <span class="tile-sub">Tuesday 7th june 2020</span>
  </div>
  <div class="date-tile tile-saturday">
    <span class="tile-title">Saturday</span>
    <span class="tile-sub">11th june</span>
  </div>
  <div class="date-tile tile-sunday">
    <span class="tile-title">Sunday</span>
    <span class="tile-sub">12th june</span>
  </div>
  <div class="date-tile tile-pick">
    <svg width="56" height="56" viewBox="0 0 56 56" aria-hidden="true">
      <rect x="4" y="8" width="48" height="44" rx="5" fill="none" stroke="#fff" stroke-width="4"/>
      <rect x="4" y="8" width="48" height="11" fill="#fff"/>
      <path d="M16 3 V13 M40 3 V13" stroke="#fff" stroke-width="4" stroke-linecap="round"/>
      <g fill="#fff">
        <rect x="11" y="25" width="7" height="6"/><rect x="21" y="25" width="7" height="6"/><rect x="31" y="25" width="7" height="6"/><rect x="41" y="25" width="6" height="6"/>
        <rect x="11" y="34" width="7" height="6"/><rect x="21" y="34" width="7" height="6"/><rect x="31" y="34" width="7" height="6"/><rect x="41" y="34" width="6" height="6"/>
        <rect x="11" y="43" width="7" height="5"/><rect x="21" y="43" width="7" height="5"/><rect x="31" y="43" width="7" height="5"/>
      </g>
    </svg>
    <span class="tile-sub">Pick a date</span>
  </div>

  <h2 class="section-title" style="top:1237px;">Vexa Picks</h2>
  <span class="section-note" style="top:1262px;">New ideas every day!</span>

  <article class="activity-card card-cooking">
    <div class="activity-photo photo-cooking" role="img" aria-label="Photo of children mixing ingredients in metal bowls at a kitchen table"></div>
    <div class="kid-tags">
      <span class="kid-tag tag-orange">SARA</span>
      <span class="kid-tag tag-yellow">FAHAD</span>
    </div>
    <div class="activity-meta">
      <span class="meta-item">
        <svg width="24" height="32" viewBox="0 0 24 32" aria-hidden="true"><path d="M12 2 C6 2 2 6.5 2 12 C2 19 12 30 12 30 C12 30 22 19 22 12 C22 6.5 18 2 12 2 Z" fill="none" stroke="#aaa" stroke-width="3"/><circle cx="12" cy="12" r="3.5" fill="#aaa"/></svg>
        Hatteen, Kuwait
      </span>
      <span class="meta-item">
        <svg width="30" height="30" viewBox="0 0 30 30" aria-hidden="true"><circle cx="15" cy="15" r="14" fill="#bbb"/><path d="M15 7 V15 L20 19" stroke="#fff" stroke-width="3" fill="none" stroke-linecap="round"/></svg>
        10:00 AM
      </span>
      <span class="meta-item">
        <svg width="30" height="30" viewBox="0 0 30 30" aria-hidden="true"><rect x="2" y="4" width="26" height="24" rx="3" fill="none" stroke="#bbb" stroke-width="2.5"/><rect x="2" y="4" width="26" height="6" fill="#bbb"/><g fill="#bbb"><rect x="7" y="14" width="4" height="3"/><rect x="13" y="14" width="4" height="3"/><rect x="19" y="14" width="4" height="3"/><rect x="7" y="20" width="4" height="3"/><rect x="13" y="20" width="4" height="3"/><rect x="19" y="20" width="4" height="3"/></g></svg>
        8-12 years
      </span>
    </div>
    <div class="card-divider"></div>
    <div class="activity-price">KD 15,000</div>
    <h3 class="activity-title">Cooking classes for beginners</h3>
    <div class="favourite-button">
      <svg width="26" height="24" viewBox="0 0 26 24" aria-label="Favourite" role="img"><path d="M13 23 L3 13 C-1 9 1 2 7 2 C10 2 12 4 13 6 C14 4 16 2 19 2 C25 2 27 9 23 13 Z" fill="#333"/></svg>
    </div>
    <div class="activity-chips">
      <span class="chip chip-vendor">WARM CRUST ACADEMY</span>
      <span class="chip chip-status">BOOKING NOW</span>
    </div>
  </article>

  <article class="activity-card card-second">
    <div class="activity-photo photo-portrait" role="img" aria-label="Portrait photo of a young boy against a dark background"></div>
    <div class="kid-tags">
      <span class="kid-tag tag-blue">LULU</span>
      <span class="kid-tag tag-purple">FAHAD</span>
    </div>
  </article>

</main>
</body>
</html>
```